Ferncrest Roam Wording For Logo & Business card

I have the logo, I just need the "Ferncrest Roam" wording to go with it, and a business card design. The only thing on the business card is the website info. We provide nature connection experiences, and bolster these efforts through writing and host a platform for community around it.

I also have an idea of what it could look like (sketch), though I'm really not sure how it would come out. I am open to the best design and happy to consider original artwork. You can see what the site is about at FerncrestRoam.example.

Contact Information for Business Card

The only thing on the business card is the website info and the design. I will put other messaging on the back.

Website lettering (FerncrestRoam.example) in Montserrat

Logo Text

Ferncrest Roam (letters optional)

Font styles to use
Other font styles liked:
• montserrat

```html
<!DOCTYPE html>
<html lang="en">
<head>
<meta charset="utf-8">
<title>Ferncrest Roam — Business Card</title>
<link rel="stylesheet" href="https://fonts.googleapis.com/css2?family=Josefin+Sans:wght@300&family=Montserrat:wght@400;500&display=swap">
<style>
  :root {
    --backdrop: #d9d9db;
    --paper: #ffffff;
    --plum-deep: #12052b;
    --plum-light: #553165;
    --ember: #f58220;
    --ink: #2a1b3d;
    --text-light: #f3eef7;
    --mark-fill: #2b1246;
  }
  * { box-sizing: border-box; margin: 0; padding: 0; }
  html, body { width: 1200px; height: 800px; overflow: hidden; }
  body {
    background: var(--backdrop);
    font-family: "Montserrat", sans-serif;
    position: relative;
  }
  .card {
    position: absolute;
    top: 245px;
    width: 540px;
    height: 309px;
    border-radius: 18px;
    overflow: hidden;
    box-shadow: 0 14px 30px rgba(0,0,0,.22);
  }
  .card--front { left: 40px; background: var(--paper); }
  .card--back {
    left: 620px;
    background: linear-gradient(120deg, var(--plum-deep) 0%, #2e1446 50%, var(--plum-light) 100%);
  }

  .info-band {
    position: absolute;
    left: 0;
    top: 156px;
    width: 100%;
    height: 153px;
    background: linear-gradient(30deg, var(--plum-deep) 0%, #2e1446 50%, var(--plum-light) 100%);
    border-top: 2px solid var(--ember);
  }
  .web-band {
    position: absolute;
    left: 0;
    bottom: 0;
    width: 100%;
    height: 76px;
    background: var(--ember);
  }

  .brand {
    position: absolute;
    display: flex;
    align-items: center;
    gap: 20px;
  }
  .brand__mark {
    border-radius: 50%;
    background: var(--mark-fill);
    flex: none;
  }
  .brand__name {
    font-family: "Josefin Sans", sans-serif;
    font-weight: 300;
    text-transform: uppercase;
    letter-spacing: .12em;
    white-space: nowrap;
  }
  .card--front .brand { left: 34px; top: 38px; }
  .card--front .brand__mark { width: 84px; height: 84px; }
  .card--front .brand__name { font-size: 32px; color: var(--ink); }

  .card--back .brand { left: 36px; top: 82px; }
  .card--back .brand__mark { width: 92px; height: 92px; background: #24103b; }
  .card--back .brand__name { font-size: 30px; color: var(--text-light); }

  .person {
    position: absolute;
    left: 40px;
    top: 222px;
  }
  .person__name { color: var(--ember); font-weight: 500; font-size: 21px; }
  .person__title { color: var(--text-light); font-size: 13px; margin-top: 2px; }

  .divider {
    position: absolute;
    left: 268px;
    top: 204px;
    width: 0;
    height: 80px;
    border-left: 1.5px solid var(--ember);
  }

  .contact {
    position: absolute;
    left: 296px;
    top: 206px;
    list-style: none;
    color: var(--text-light);
    font-size: 12px;
  }
  .contact li { display: flex; align-items: center; gap: 8px; line-height: 24px; white-space: nowrap; }
  .contact svg { flex: none; }

  .website {
    position: absolute;
    left: 0;
    bottom: 24px;
    width: 100%;
    text-align: center;
    color: var(--paper);
    font-size: 17px;
    font-weight: 500;
    letter-spacing: .08em;
  }
</style>
</head>
<body>

<section class="card card--front" aria-label="Business card front">
  <div class="info-band"></div>

  <div class="brand">
    <span class="brand__mark"></span>
    <span class="brand__name">Ferncrest Roam</span>
  </div>

  <div class="person">
    <p class="person__name">Dana Whitlow</p>
    <p class="person__title">President</p>
  </div>

  <span class="divider" aria-hidden="true"></span>

  <ul class="contact">
    <li>
      <svg width="12" height="12" viewBox="0 0 12 12" aria-hidden="true"><rect x="3" y="0.5" width="6" height="11" rx="1.2" fill="none" stroke="#f58220" stroke-width="1.3"/></svg>
      555-014-2290
    </li>
    <li>
      <svg width="12" height="12" viewBox="0 0 12 12" aria-hidden="true"><rect x="0.5" y="2" width="11" height="8" fill="#f58220"/><polyline points="0.5,2 6,7 11.5,2" fill="none" stroke="#2a1240" stroke-width="1"/></svg>
      info@ferncrestroam.example
    </li>
    <li>
      <svg width="12" height="12" viewBox="0 0 12 12" aria-hidden="true"><circle cx="6" cy="6" r="5.5" fill="#f58220"/><ellipse cx="6" cy="6" rx="2.2" ry="5.5" fill="none" stroke="#2a1240" stroke-width=".9"/><line x1="0.5" y1="6" x2="11.5" y2="6" stroke="#2a1240" stroke-width=".9"/></svg>
      ferncrestroam.example
    </li>
  </ul>
</section>

<section class="card card--back" aria-label="Business card back">
  <div class="brand">
    <span class="brand__mark"></span>
    <span class="brand__name">Ferncrest Roam</span>
  </div>

  <div class="web-band"></div>
  <p class="website">www.FerncrestRoam.example</p>
</section>

</body>
</html>
```